Bench Advertisement - We Buy Houses Design Needed

Need a catchy, simple but elegant design for bus benches to advertise our company.

We need our website, or phone number, and a smal description (1-2 bulletpoints of what we do and what we offer)

The tricky part is for the designer to fit everything and make the website name as part of the title and fitting everything so that people passing by on the street can see what we offer.

Our website is quickdealhomebuyer.com - (916) 555-0143

Something simple but something that catches the eye of walking pedestrians, and drivers driving by the bench.

Our company buys houses, any condition, any situation, we buy houses for cash and close quickly. You can use this description to create a few bulletpoints however you like. Must follow dimensions in attachment.

Target Market(s)

People in foreclosure, about to lose their homes, people that need a quick cash sale of their property

Industry/Entity Type

Real Estate

Requirements
Must have
• catchy, website name, phone number, few brief bulletpoints about what we offer, colors that will catch peoples eye while walking or driving - advertisement will be placed on bus benches - visit our website to see the type of houses we buy - Also have more work for winner of design with possible bonuses
Nice to have
• Feel free to use description or images on our website - make sure the description is just bullet points and it fits with the overall theme / size of the advertisement - Bold bright colors - put yourself in their shoes (if you were going through financial difficulties and about to lose your house to foreclosure or auction, what would you want to see to pick up the phone and call us for a quick sale of your house?) (or if you have a house that you are having a problem with, problem renters, unkept/beat up house, what would make you want to call us and sell your house to us?)

```html
<!DOCTYPE html>
<html lang="en">
<head>
<meta charset="utf-8">
<title>Bench Advertisement – QuickDeal Home Buyer</title>
<link href="https://fonts.googleapis.com/css2?family=Anton&family=Lato:wght@400&display=swap" rel="stylesheet">
<style>
  :root {
    --orange: #ee8b38;
    --orange-light: #f3a462;
    --ink: #000000;
    --paper: #ffffff;
    --caption: #5a5a5a;
  }
  html, body {
    margin: 0;
    padding: 0;
    width: 1200px;
    height: 1200px;
    overflow: hidden;
    background: var(--paper);
  }
  .sheet {
    position: relative;
    width: 1200px;
    height: 1200px;
  }
  .bench-ad {
    position: absolute;
    left: 206px;
    width: 808px;
    display: block;
  }
  .bench-ad--type { top: 300px; height: 228px; }
  .bench-ad--icons { top: 623px; height: 226px; }
  .caption {
    position: absolute;
    left: 0;
    width: 1200px;
    margin: 0;
    text-align: center;
    font-family: "Lato", sans-serif;
    font-weight: 400;
    font-size: 22px;
    color: var(--caption);
  }
  .caption--type { top: 548px; left: 24px; }
  .caption--icons { top: 878px; }
  .ad-type { font-family: "Anton", sans-serif; font-weight: 400; }
  .fill-orange { fill: var(--orange); }
  .fill-light { fill: var(--orange-light); }
  .fill-ink { fill: var(--ink); }
  .fill-paper { fill: var(--paper); }
</style>
</head>
<body>
<main class="sheet">

  <svg class="bench-ad bench-ad--type" viewBox="0 0 1010 285" aria-label="Bench ad: sell your house fast">
    <rect class="fill-orange" width="1010" height="285"/>
    <text class="ad-type bullets fill-ink" x="24" y="44" font-size="24" textLength="962" lengthAdjust="spacing">• We buy houses for cash   • Any condition, any situation   • We close quickly</text>
    <text class="ad-type headline" x="-6" y="178" font-size="130" textLength="1016" lengthAdjust="spacingAndGlyphs">
      <tspan class="fill-paper">sell</tspan><tspan class="fill-ink">your</tspan><tspan class="fill-paper">house</tspan><tspan class="fill-ink">fast</tspan>
    </text>
    <text class="ad-type website" x="24" y="248" font-size="38" textLength="541" lengthAdjust="spacingAndGlyphs">
      <tspan class="fill-paper">quick</tspan><tspan class="fill-ink">deal</tspan><tspan class="fill-paper">home</tspan><tspan class="fill-ink">buyer</tspan><tspan class="fill-paper">.com</tspan>
    </text>
    <text class="ad-type phone fill-ink" x="580" y="248" font-size="38" textLength="248" lengthAdjust="spacingAndGlyphs">(916) 555-0143</text>
    <g class="brand-name">
      <rect class="fill-paper" x="846" y="222" width="12" height="12"/>
      <text class="ad-type fill-paper" x="864" y="234" font-size="17" textLength="130" lengthAdjust="spacingAndGlyphs">QuickDeal Home Buyer</text>
    </g>
  </svg>

  <p class="caption caption--type">Keeping it simple</p>

  <svg class="bench-ad bench-ad--icons" viewBox="0 0 1007 282" aria-label="Bench ad: your house unlocks cash">
    <rect class="fill-orange" width="1007" height="282"/>
    <text class="ad-type bullets fill-ink" x="42" y="40" font-size="20" textLength="262" lengthAdjust="spacing">• Cash  • Any condition  • Fast close</text>
    <text class="ad-type word-your fill-ink" x="42" y="168" font-size="110" textLength="262" lengthAdjust="spacingAndGlyphs">your</text>
    <rect class="fill-light pictogram-area" x="318" y="0" width="640" height="200" role="img" aria-label="Pictograms: a house, an open padlock and a money bag, suggesting cash unlocked from a home"/>
    <text class="ad-type website" x="24" y="250" font-size="38" textLength="541" lengthAdjust="spacingAndGlyphs">
      <tspan class="fill-paper">quick</tspan><tspan class="fill-ink">deal</tspan><tspan class="fill-paper">home</tspan><tspan class="fill-ink">buyer</tspan><tspan class="fill-paper">.com</tspan>
    </text>
    <text class="ad-type phone fill-ink" x="578" y="250" font-size="38" textLength="248" lengthAdjust="spacingAndGlyphs">(916) 555-0143</text>
    <g class="brand-name">
      <rect class="fill-paper" x="844" y="224" width="12" height="12"/>
      <text class="ad-type fill-paper" x="862" y="236" font-size="17" textLength="130" lengthAdjust="spacingAndGlyphs">QuickDeal Home Buyer</text>
    </g>
  </svg>

  <p class="caption caption--icons">... Use of pictograms to suggest unlocking cash tied up in a house</p>

</main>
</body>
</html>
```